Trueline Referral Hub needs updated website.

Our current website was designed on wix.com. (www.truelinereferralhub.example).
We would like something a little more customized for what our company offers. Trueline Referral Hub is a company specializing in connecting consumers with trustworthy and affordable service professionals. We need the website to be approachable and easy to use, while conveying our "Trueline" reputation.
Reason: Our project is now guaranteed. Please send your ideas. Thank you!
Target Market(s)
Homeowners
Industry/Entity Type
It Company
Look and feel
Each slider illustrates characteristics of the customer's brand and the style your logo design should communicate.

```html
<!DOCTYPE html>
<html lang="en">
<head>
<meta charset="utf-8">
<title>Trueline Referral Hub</title>
<link href="https://fonts.googleapis.com/css2?family=Open+Sans:wght@400;600;700&display=swap" rel="stylesheet">
<style>
:root{
  --green:#7ab32e;
  --green-dark:#4e7f10;
  --ink:#3a3a3a;
  --text:#333;
  --muted:#888;
  --rule:#d8d8d8;
  --hero-bg:#eef3f6;
  --white:#fff;
}
*{margin:0;padding:0;box-sizing:border-box}
html,body{width:795px;height:1200px;overflow:hidden;background:var(--white)}
body{font-family:"Open Sans",Arial,sans-serif;color:var(--text);position:relative}
.site{position:relative;width:795px;height:1200px}

.header{position:absolute;top:0;left:0;width:795px;height:110px}
.brand{position:absolute;left:68px;top:30px;display:flex;align-items:center;gap:10px}
.brand-dot{width:40px;height:40px;border-radius:50%;background:var(--green)}
.brand-name{font-size:25px;font-weight:700;color:var(--ink);line-height:1}
.call{position:absolute;right:70px;top:32px;text-align:left}
.call-label{font-size:15px;color:var(--ink)}
.call-number{font-size:19px;font-weight:700;color:var(--ink);margin-top:2px}

.nav{position:absolute;top:110px;left:0;width:795px;height:46px;border-top:1px solid var(--green);border-bottom:1px solid var(--rule)}
.nav-home{position:absolute;left:68px;top:0;width:111px;height:45px;background:var(--green);color:var(--white);font-weight:700;font-size:14px;display:flex;align-items:center;justify-content:center}
.nav-links{position:absolute;left:205px;right:70px;top:0;height:45px;display:flex;justify-content:space-between;align-items:center}
.nav-links span{font-size:13.5px;color:var(--ink);padding:0 24px;border-left:1px solid var(--rule);line-height:20px}
.nav-links span:first-child{border-left:none;padding-left:26px}
.nav-links span:last-child{padding-right:0}

.hero{position:absolute;top:156px;left:0;width:795px;height:298px;background:var(--hero-bg);overflow:hidden}
.hero-photo{position:absolute;right:0;top:0;width:415px;height:298px;background:linear-gradient(100deg,#eef3f6 0%,#e2c4ad 30%,#6b4a3a 60%,#e9eef2 100%)}
.hero-copy{position:absolute;left:68px;top:42px;width:280px}
.hero-title{font-size:28px;font-weight:400;color:var(--ink);line-height:36px}
.hero-title strong{display:block;color:var(--green);font-weight:700;font-size:32px;line-height:44px}
.hero-text{font-size:11.5px;line-height:16px;color:var(--ink);margin-top:14px}
.dots{position:absolute;left:69px;top:238px;display:flex;gap:3px}
.dots i{width:11px;height:11px;border-radius:50%;background:#b9bdc0}
.dots i:first-child{background:var(--green)}

.intro{position:absolute;top:454px;left:0;width:795px;height:83px;text-align:center}
.intro h2{font-size:22px;font-weight:700;color:var(--green);margin-top:18px}
.intro p{font-size:8.5px;color:var(--ink);margin-top:8px}

.services{position:absolute;top:537px;left:0;width:795px;height:179px;background:var(--green-dark)}
.arrow{position:absolute;top:69px;width:49px;height:39px;background:var(--white);display:flex;align-items:center;justify-content:center}
.arrow.prev{left:69px}.arrow.next{left:677px}
.service{position:absolute;top:22px;width:130px;color:var(--white)}
.service h3{font-size:12px;font-weight:700}
.service p{font-size:8.6px;line-height:13.2px;margin-top:10px}
.service .more{font-size:8.5px;font-weight:700;margin-top:14px;display:block}

.about{position:absolute;top:716px;left:0;width:795px;height:330px}
.about h2{position:absolute;left:68px;top:22px;font-size:31px;font-weight:700;color:var(--green-dark)}
.about .lead{position:absolute;left:68px;top:76px;font-size:19px;line-height:25px;color:var(--ink);width:400px}
.about .lead em{font-style:normal;color:var(--green-dark)}
.about .body{position:absolute;left:68px;top:134px;width:395px;font-size:13px;line-height:16.5px;color:var(--ink)}
.btn{position:absolute;left:69px;top:275px;width:93px;height:34px;background:var(--green-dark);color:var(--white);font-size:13.5px;display:flex;align-items:center;justify-content:center}
.divider{position:absolute;left:492px;top:20px;width:1px;height:290px;background:var(--rule)}
.offer-title{position:absolute;left:540px;top:24px;font-size:23px;font-weight:700;color:var(--green-dark)}
.offer{position:absolute;left:540px;width:190px;display:flex;gap:7px}
.offer-photo{width:62px;height:62px;flex:none;border:1px solid #e2e2e2}
.offer h4{font-size:9px;font-weight:400;color:var(--green-dark);margin-top:-1px}
.offer p{font-size:7.8px;line-height:12px;color:var(--muted);margin-top:5px;font-family:Arial,sans-serif}

.footer{position:absolute;top:1046px;left:0;width:795px;height:154px;background:var(--green-dark);color:var(--white)}
.footer-brand{position:absolute;left:70px;top:32px;display:flex;align-items:center;gap:7px}
.footer-brand .brand-dot{width:30px;height:30px;background:var(--white)}
.footer-brand .brand-name{color:var(--white);font-size:17px}
.copyright{position:absolute;left:70px;top:82px;font-size:8.5px}
.footer-nav{position:absolute;right:70px;top:24px;display:flex;gap:19px;font-size:8.5px}
.address{position:absolute;right:70px;top:56px;font-size:11.5px}
.phone{position:absolute;right:70px;top:82px;font-size:14.5px;color:#b9dc7a}
.email{position:absolute;right:70px;top:102px;font-size:11.5px}
</style>
</head>
<body>
<div class="site">
  <header class="header">
    <div class="brand"><span class="brand-dot"></span><span class="brand-name">Trueline</span></div>
    <div class="call">
      <div class="call-label">Call Us Now:</div>
      <div class="call-number">1-555-010-4821</div>
    </div>
  </header>

  <nav class="nav">
    <div class="nav-home">HOME</div>
    <div class="nav-links">
      <span>ABOUT TRUELINE</span><span>SERVICES</span><span>OUR NETWORK</span><span>CONTACT US</span>
    </div>
  </nav>

  <section class="hero">
    <div class="hero-photo" role="img" aria-label="Smiling customer support agent wearing a headset"></div>
    <div class="hero-copy">
      <h1 class="hero-title">SOMETIMES ALL<br>YOU REALLY NEED IS <strong>A TRUELINE.</strong></h1>
      <p class="hero-text">Praesent vestibulum aenean nonummy hendrerit mauris. Hasellus porta. Fusce suscipit varius mi cum sociis natoque penatibus et magnis.</p>
    </div>
    <div class="dots"><i></i><i></i><i></i><i></i></div>
  </section>

  <section class="intro">
    <h2>TRUELINE REFERRAL HUB</h2>
    <p>Praesent vestibulum aenean nonummy hendrerit mauris. Hasellus porta. Fusce suscipit varius mi cum sociis natoque penatibus et magnis.</p>
  </section>

  <section class="services">
    <div class="arrow prev"><svg width="16" height="20" viewBox="0 0 16 20"><path d="M12 2 L4 10 L12 18" fill="none" stroke="#4e7f10" stroke-width="4"/></svg></div>
    <div class="service" style="left:153px">
      <h3>Heating</h3>
      <p>Praesent vestibulum aenean nonummy hendrerit mauris. Hasellus porta. Fusce suscipit varius mi cum sociis natoque penatibus et magnis dis parturi-ent montes nascetur.</p>
      <span class="more">READ MORE</span>
    </div>
    <div class="service" style="left:332px">
      <h3>Air Conditioning</h3>
      <p>Praesent vestibulum aenean nonummy hendrerit mauris. Hasellus porta. Fusce suscipit varius mi cum sociis natoque penatibus et magnis dis parturi-ent montes nascetur.</p>
      <span class="more">READ MORE</span>
    </div>
    <div class="service" style="left:509px;width:140px">
      <h3>Automotive Maintenance</h3>
      <p>Praesent vestibulum aenean nonummy hendrerit mauris. Hasellus porta. Fusce suscipit varius mi cum sociis natoque penatibus et magnis dis parturi-ent montes nascetur.</p>
      <span class="more">READ MORE</span>
    </div>
    <div class="arrow next"><svg width="16" height="20" viewBox="0 0 16 20"><path d="M4 2 L12 10 L4 18" fill="none" stroke="#4e7f10" stroke-width="4"/></svg></div>
  </section>

  <section class="about">
    <h2>Trueline Referral Hub</h2>
    <p class="lead"><em>Connecting YOU</em> with the most reputable and affordable businesses in Saint Louis.</p>
    <p class="body">The founders of Trueline Referral Hub have over 30 years in the St. Louis Automotive and HVAC industries. In both markets, among many others, one thing is clear: A consumer gets better service at a lower price when they know who to call.&nbsp; Opening up a phonebook, newspa-per, or randomly selected online business could cost you hundreds, even thousands of dollars too much money.</p>
    <div class="btn">Know More</div>
    <div class="divider"></div>
    <h3 class="offer-title">WE OFFER</h3>
    <div class="offer" style="top:70px">
      <div class="offer-photo" role="img" aria-label="Businessman in a white shirt and tie" style="background:linear-gradient(180deg,#dfe6ec,#f4f4f4 60%,#2c3440)"></div>
      <div><h4>CALL ANSWERING SERVICES</h4><p>Accusamu dolore masugharum quidemed rerum facilis iustossi mos ducimus qui blanditiistes</p></div>
    </div>
    <div class="offer" style="top:157px">
      <div class="offer-photo" role="img" aria-label="Businesswoman raising her arms under a bright sky" style="background:linear-gradient(180deg,#cfe4f3,#f2f7fb 60%,#3a3f47)"></div>
      <div><h4>24/7 SUPPORT SERVICES</h4><p>Accusamu dolore masugharum quidemed rerum facilis iustossi mos ducimus qui blanditiistes</p></div>
    </div>
    <div class="offer" style="top:244px">
      <div class="offer-photo" role="img" aria-label="Smiling woman holding a coffee cup" style="background:linear-gradient(180deg,#e6ecf0,#d9c8b4 55%,#cfdbe4)"></div>
      <div><h4>NETWORK MANAGEMENT</h4><p>Accusamu dolore masugharum quidemed rerum facilis iustossi mos ducimus qui blanditiistes</p></div>
    </div>
  </section>

  <footer class="footer">
    <div class="footer-brand"><span class="brand-dot"></span><span class="brand-name">Trueline</span></div>
    <p class="copyright">© copyrights Trueline Referral Hub Inc. All rights reserved</p>
    <div class="footer-nav"><span>Home</span><span>About Trueline</span><span>Services</span><span>Our network</span><span>Contact us</span></div>
    <p class="address">450 Meridian Street, Saint Louis, Missouri 63101</p>
    <p class="phone">Phone: 1-555-010-4821</p>
    <p class="email">E-mail: info@truelinereferralhub.example</p>
  </footer>
</div>
</body>
</html>
```